Coupon/promo code site

I am looking for a one page website that will provide a list of coupon codes that are used at checkout when buying something online. The site will only have coupon codes for one online retailer. I would like this to be generic (i.e. not specific to any one retailer). I would like to have some interchangeable parts so that I could later customize the site so that it is specific to any given retailer.

I envision the site having a list of coupon codes with information about each code like when it expires and what it provides. For example there would be a: code, expiration date, short description or name, and a longer description (i.e. details).
Updates

Project Deadline Extended
Reason: I am going to submit a wire frame that provides a better idea of what I am looking for.

I have uploaded a wire frame that gives a more clear indication of what I am looking for.  Please see this before submitting designs.  If you have already submitted a design, please revise your design considering the wire frame I have provided.

Thanks,
Brent

Target Market(s)

Someone who is shopping online and searching for a specific retailers coupon codes

Industry/Entity Type

Coupon

Requirements
Must have
• I would like the site to have a white or light colored background.

I need a place or two where I can interchangeably place different retailers' logos.

The web page should have a title like, "[retailer's] online coupon code"

In addition to a list or table of coupon codes, there should below this be a list or table of special offers or sale items.

At the very bottom in a way that is not too noticeable, it should say, "This coupon site was created by Pelvo Deals."

There should be a section (probably on the right side) that allows a user to submit their email address to be notified in the future of specials/deals for this retailer.

There should be a nice looking link that goes to the online retailer's website.
Nice to have
• Example sites with a look and feel that I like are:

http://www.quorvane.com/
https://thebrattle.com/
http://www.plimworks.com

This is an example of a site with coupon codes for just one retailer. This site is a little too busy, but you get the idea:
www.makenforth.com/coupon-codes‎

```html
<!DOCTYPE html>
<html lang="en">
<head>
<meta charset="utf-8">
<title>Company Name Promo Codes</title>
<link href="https://fonts.googleapis.com/css2?family=Days+One&family=Fjalla+One&family=Open+Sans:wght@400&family=Arimo:wght@400;700&display=swap" rel="stylesheet">
<style>
  :root {
    --blue: #0b8fd4;
    --title-blue: #1b86c4;
    --red: #e8191c;
    --panel: #e4e4e4;
    --card: #ffffff;
    --ink: #333333;
    --muted: #555555;
    --code: #555555;
    --code-active: #8a8a8a;
    --footer: #e2e2e2;
    --rule: #cfcfcf;
  }
  * { box-sizing: border-box; margin: 0; padding: 0; }
  html, body { width: 850px; height: 1200px; overflow: hidden; background: #fff; }
  body { position: relative; font-family: "Arimo", Arial, sans-serif; color: var(--ink); }

  .site-header { position: absolute; left: 0; top: 0; width: 850px; height: 98px; border-bottom: 1px dashed var(--rule); }
  .logo-slot { position: absolute; left: 17px; top: 22px; width: 193px; height: 56px; background: var(--red); border-radius: 12px; }
  .page-title { position: absolute; left: 245px; top: 31px; font-family: "Days One", sans-serif; font-size: 31px; color: var(--title-blue); letter-spacing: .5px; font-weight: 400; white-space: nowrap; }

  .welcome { position: absolute; left: 0; top: 98px; width: 850px; height: 156px; border-bottom: 1px dashed var(--rule); text-align: center; font-family: "Open Sans", sans-serif; font-weight: 400; font-size: 26px; line-height: 31px; color: #333; padding-top: 31px; }

  .code-panel { position: absolute; left: 6px; width: 599px; background: var(--panel); border-radius: 13px; padding: 7px 9px; }
  .featured { top: 266px; height: 507px; }
  .specials { top: 804px; height: 282px; }
  .panel-head { height: 35px; background: var(--blue); border-radius: 8px; padding: 2px; margin: 0 -2px 10px -2px; }
  .panel-head h2 { height: 100%; border: 1px dashed rgba(255,255,255,.85); border-radius: 6px; font-family: "Days One", sans-serif; font-weight: 400; font-size: 19px; color: #fff; line-height: 29px; padding-left: 12px; white-space: nowrap; }

  .offer { position: relative; height: 105px; background: var(--card); border-radius: 7px; margin-bottom: 8px; }
  .offer .title { position: absolute; left: 16px; top: 11px; font-size: 15.5px; color: #222; white-space: nowrap; }
  .offer .desc { position: absolute; left: 16px; top: 32px; width: 300px; font-size: 9.5px; line-height: 12px; color: var(--muted); }
  .offer .desc.single { width: 340px; white-space: nowrap; }
  .offer .expires { position: absolute; left: 16px; bottom: 17px; font-size: 10.5px; color: var(--red); }
  .offer .shop { position: absolute; right: 16px; bottom: 17px; font-size: 12.5px; color: var(--muted); white-space: nowrap; }
  .offer .shop a { color: #333; font-weight: 700; text-decoration: none; margin-left: 5px; }
  .offer .code-label { position: absolute; right: 123px; top: 11px; font-size: 15.5px; color: #333; }
  .offer .code { position: absolute; right: 12px; top: 9px; width: 103px; height: 24px; border-radius: 7px; background: var(--code); color: #fff; font-weight: 700; font-size: 12px; letter-spacing: 1px; text-align: center; line-height: 24px; }
  .offer .code.revealed { background: var(--code-active); }

  .copy-tip { position: absolute; left: 486px; top: 287px; width: 109px; height: 31px; background: var(--red); border-radius: 9px; color: #fff; font-size: 10.5px; text-align: center; line-height: 31px; }
  .copy-tip::after { content: ""; position: absolute; left: 44px; bottom: -6px; border-left: 7px solid transparent; border-right: 7px solid transparent; border-top: 7px solid var(--red); }

  .newsletter { position: absolute; left: 622px; top: 267px; width: 214px; height: 242px; background: var(--panel); }
  .newsletter .band { height: 82px; margin-top: 6px; background: var(--blue); border-top: 1px dashed rgba(255,255,255,.8); border-bottom: 1px dashed rgba(255,255,255,.8); display: flex; align-items: center; padding-left: 13px; gap: 12px; }
  .newsletter .band h3 { font-family: "Fjalla One", sans-serif; font-weight: 400; color: #fff; font-size: 23px; line-height: 26px; }
  .newsletter p { font-size: 10.5px; line-height: 12.5px; color: var(--muted); text-align: center; padding: 17px 14px 0; }
  .newsletter .email { margin: 15px 9px 0; height: 22px; background: #fff; border: 1px solid #cfcfcf; border-radius: 3px; font-size: 9.5px; line-height: 20px; padding-left: 10px; color: #333; }
  .newsletter .subscribe { margin: 10px 0 0 11px; width: 93px; height: 28px; border-radius: 4px; background: var(--blue); border: 2px solid #6cc0ec; color: #fff; font-family: "Fjalla One", sans-serif; font-size: 16px; text-align: center; line-height: 23px; }

  .share { position: absolute; left: 622px; top: 518px; width: 214px; height: 104px; background: var(--panel); }
  .share .band { height: 40px; margin-top: 6px; background: var(--blue); border-top: 1px dashed rgba(255,255,255,.8); border-bottom: 1px dashed rgba(255,255,255,.8); text-align: center; font-family: "Fjalla One", sans-serif; color: #fff; font-size: 23px; line-height: 37px; }
  .share ul { list-style: none; display: flex; gap: 6px; padding: 8px 0 0 22px; }
  .share li { width: 37px; height: 37px; background: #8c8c8c; color: #fff; font-size: 9px; text-align: center; line-height: 37px; }

  .site-footer { position: absolute; left: 0; top: 1113px; width: 850px; height: 70px; background: var(--footer); text-align: center; padding-top: 20px; }
  .site-footer .copyright { font-size: 11px; color: #333; }
  .site-footer .credit { font-size: 9.5px; color: #888; margin-top: 6px; letter-spacing: .3px; }
</style>
</head>
<body>

<header class="site-header">
  <div class="logo-slot" role="img" aria-label="Retailer logo placeholder"></div>
  <h1 class="page-title">Company Name Promo Codes</h1>
</header>

<section class="welcome">
  Welcome to the Company Name promo page.<br>
  Here you will find the best and most up to datepromo codes<br>
  available directly form Company name
</section>

<section class="code-panel featured">
  <div class="panel-head"><h2>Featured Promo Codes</h2></div>

  <article class="offer">
    <div class="title">$51.26 Average savings on Brightmart.com</div>
    <div class="desc single">Receive up to 60% off + Extra 20% off Select Jewelry &amp; Watches.</div>
    <div class="code-label">Coupon Code:</div>
    <div class="code revealed">12FOR12</div>
    <div class="expires">Offer Expires: Aug 24, 2013</div>
    <div class="shop">Use this code when shopping at :<a href="#">Brightmart.com</a></div>
  </article>

  <article class="offer">
    <div class="title">Free Shipping</div>
    <div class="desc">Receive free shipping on orders over $50. The description could wrap like this</div>
    <div class="code-label">Coupon Code:</div>
    <div class="code"></div>
    <div class="expires">Offer Expires: Aug 24, 2013</div>
    <div class="shop">Use this code when shopping at :<a href="#">Brightmart.com</a></div>
  </article>

  <article class="offer">
    <div class="title">$51.26 Average savings on Brightmart.com</div>
    <div class="desc single">Receive up to 60% off + Extra 20% off Select Jewelry &amp; Watches.</div>
    <div class="code-label">Coupon Code:</div>
    <div class="code"></div>
    <div class="expires">Offer Expires: Aug 24, 2013</div>
    <div class="shop">Use this code when shopping at :<a href="#">Brightmart.com</a></div>
  </article>

  <article class="offer">
    <div class="title">Free Shipping</div>
    <div class="desc">Receive free shipping on orders over $50. The description could wrap like this</div>
    <div class="code-label">Coupon Code:</div>
    <div class="code"></div>
    <div class="expires">Offer Expires: Aug 24, 2013</div>
    <div class="shop">Use this code when shopping at :<a href="#">Brightmart.com</a></div>
  </article>
</section>

<div class="copy-tip">Click to copy code</div>

<section class="code-panel specials">
  <div class="panel-head"><h2>Special Offers &amp; Sales Items</h2></div>

  <article class="offer">
    <div class="title">$51.26 Average savings on Brightmart.com</div>
    <div class="desc single">Receive up to 60% off + Extra 20% off Select Jewelry &amp; Watches.</div>
    <div class="code-label">Coupon Code:</div>
    <div class="code"></div>
    <div class="expires">Offer Expires: Aug 24, 2013</div>
    <div class="shop">Use this code when shopping at :<a href="#">Brightmart.com</a></div>
  </article>

  <article class="offer">
    <div class="title">Free Shipping</div>
    <div class="desc">Receive free shipping on orders over $50. The description could wrap like this</div>
    <div class="code-label">Coupon Code:</div>
    <div class="code"></div>
    <div class="expires">Offer Expires: Aug 24, 2013</div>
    <div class="shop">Use this code when shopping at :<a href="#">Brightmart.com</a></div>
  </article>
</section>

<aside class="newsletter">
  <div class="band">
    <svg width="58" height="48" viewBox="0 0 58 48" aria-hidden="true">
      <path d="M3 20 L29 3 L55 20 L55 46 L3 46 Z" fill="#fff"/>
      <rect x="13" y="11" width="32" height="22" rx="2" fill="#fff" stroke="#0b8fd4" stroke-width="2"/>
      <line x1="21" y1="17" x2="37" y2="17" stroke="#0b8fd4" stroke-width="2.5"/>
      <line x1="21" y1="22" x2="37" y2="22" stroke="#0b8fd4" stroke-width="2.5"/>
      <line x1="21" y1="27" x2="37" y2="27" stroke="#0b8fd4" stroke-width="2.5"/>
      <path d="M3 20 L29 36 L55 20" fill="none" stroke="#0b8fd4" stroke-width="2"/>
      <path d="M3 46 L23 32 M55 46 L35 32" stroke="#0b8fd4" stroke-width="2"/>
    </svg>
    <h3>Never Miss<br>Another Deal!</h3>
  </div>
  <p>Our promotions are updated frequently, so be sure to sign-up for our newsletter to receive notification of new promo codes and exclusive offers.</p>
  <div class="email">Enter Your Email Address Here</div>
  <div class="subscribe">subscribe</div>
</aside>

<aside class="share">
  <div class="band">share this site</div>
  <ul>
    <li>Folk</li>
    <li>Chirp</li>
    <li>Pinly</li>
    <li>Plux</li>
  </ul>
</aside>

<footer class="site-footer">
  <div class="copyright">Copyright © 2013 dealnook.com All rights reserved.</div>
  <div class="credit">This coupon site was created by Pelvo Deals</div>
</footer>

</body>
</html>
```